The book will contain the papers written by presenters at the Fresh Horizons in Beyond Contact conference held by the Institute for Luminous and Awareness Research. There will be something like 19 chapters, each about a different method people are using today to have afterlife communication with loved ones on the other side. The cover must be upbeat, inspiring, full of joy and life. Nothing with ghosts or cemeteries or skeletons or hauntings. It's about family members communicating with loved ones who are alive and well, just living on a different plane. Any image of uniting, love, and togetherness is a plus. The author name is Institute for Luminous and Awareness Research.

Industry/Entity Type

Communication

```html
<!DOCTYPE html>
<html lang="en">
<head>
<meta charset="utf-8">
<title>Fresh Horizons in Beyond Contact — Book Cover</title>
<link href="https://fonts.googleapis.com/css2?family=Lilita+One&family=Philosopher:wght@700&display=swap" rel="stylesheet">
<style>
  :root {
    --backdrop: #efefef;
    --stone-dark: #2b2420;
    --stone-mid: #5a4d43;
    --stone-light: #8a7a6c;
    --glow: #ffffff;
    --sky-warm: #f3c9a0;
    --sky-rose: #e9b8c0;
    --hill: #9a8a6a;
    --grass: #8a8a3a;
    --grass-dark: #5f6a28;
    --maroon: #6e1a14;
    --banner: #24386a;
    --banner-edge: #1a2a55;
    --white: #ffffff;
    --sky-blue: #4da3e6;
    --gold: #d9a41f;
  }
  * { margin: 0; padding: 0; box-sizing: border-box; }
  html, body {
    width: 1200px; height: 871px; overflow: hidden;
    background: var(--backdrop);
  }
  .cover {
    position: absolute; left: 307px; top: 0;
    width: 586px; height: 871px; overflow: hidden;
  }
  .doorway-frame {
    position: absolute; inset: 0;
    background: linear-gradient(90deg, var(--stone-dark) 0%, var(--stone-mid) 3%, var(--stone-dark) 6%, transparent 6%, transparent 94%, var(--stone-dark) 94%, var(--stone-mid) 97%, var(--stone-dark) 100%),
                linear-gradient(180deg, var(--stone-mid), var(--stone-dark));
  }
  .scene {
    position: absolute; left: 34px; right: 34px; top: 0; bottom: 28px;
    border-radius: 60px 60px 0 0 / 40px 40px 0 0;
    background:
      radial-gradient(ellipse 55% 42% at 50% 48%, var(--glow) 0%, rgba(255,255,255,0.92) 45%, rgba(255,255,255,0) 100%),
      linear-gradient(180deg, #fbf6f2 0%, var(--sky-rose) 22%, var(--sky-warm) 30%, var(--hill) 38%, #e8e2d8 48%, #f4f0ea 72%, var(--grass) 80%, var(--grass-dark) 100%);
  }
  .author {
    position: absolute; top: 58px; left: 0; width: 100%;
    text-align: center;
    font-family: "Philosopher", sans-serif; font-weight: 700;
    font-size: 29px; line-height: 33px; letter-spacing: 0.5px;
    color: var(--maroon); text-transform: uppercase;
  }
  .title-banner {
    position: absolute; left: 30px; top: 341px; width: 530px; height: 231px;
    background: var(--banner);
    border-top: 2px solid var(--banner-edge); border-bottom: 2px solid var(--banner-edge);
    font-family: "Lilita One", sans-serif; text-transform: uppercase;
    color: var(--white); text-align: center;
    display: flex; flex-direction: column; justify-content: center;
  }
  .title-line { display: block; line-height: 1; }
  .title-line--top { font-size: 51px; letter-spacing: 1px; }
  .title-line--mid { font-size: 72px; margin: 4px 0; }
  .title-line--mid .small { font-size: 38px; vertical-align: 24px; margin-right: 4px; }
  .accent-blue { color: var(--sky-blue); }
  .accent-gold { color: var(--gold); }
  .title-line--bottom { font-size: 58px; letter-spacing: 1px; }
</style>
</head>
<body>
  <main class="cover">
    <div class="doorway-frame" role="img" aria-label="Carved stone doorway framing the scene"></div>
    <div class="scene" role="img" aria-label="Sunlit valley with misty mountains, bright radiant light and grassy ground with a ring of white stones"></div>
    <p class="author">Institute for Luminous<br>and Awareness Research</p>
    <h1 class="title-banner">
      <span class="title-line title-line--top">Fresh Horizons</span>
      <span class="title-line title-line--mid"><span class="small">In</span><span class="accent-blue">Bey</span><span class="accent-gold">ond</span></span>
      <span class="title-line title-line--bottom">Contact</span>
    </h1>
  </main>
</body>
</html>
```